PERI VALORE

We need a letterhead design for an Image & Etiquette Consultancy company based in Singapore.

The services we provide are Personal Image Consultation, Image & Etiquette Workshop for schools and corporate.

The design should have our corporate colour as seen in the logo files I have uploaded.

Since our company helps clients with their image, the design should be aesthetically very appealing. It should reflect a very classy & elegant feel.

I will print the letterhead using my printer but most of the time will use it to write letters to my clients therefore the format should include MS Word.

```html
<!DOCTYPE html>
<html lang="en">
<head>
<meta charset="utf-8">
<title>Peri Valore Letterhead</title>
<link href="https://fonts.googleapis.com/css2?family=Josefin+Sans:wght@300;400&display=swap" rel="stylesheet">
<style>
  :root {
    --backdrop: #e9e9e9;
    --paper: #ffffff;
    --brand-purple: #3d1f4f;
    --brand-gold: #d4a93a;
    --muted-gold: #c9a24a;
  }
  html, body {
    margin: 0;
    width: 1200px;
    height: 795px;
    overflow: hidden;
    background: var(--backdrop);
  }
  .canvas {
    width: 1200px;
    height: 795px;
    display: flex;
    align-items: center;
    justify-content: center;
  }
  .letterhead {
    width: 520px;
    height: 735px;
    background: var(--paper);
    box-shadow: 0 2px 10px rgba(0,0,0,0.12);
    position: relative;
    font-family: "Josefin Sans", sans-serif;
  }
  .header-band {
    position: absolute;
    top: 38px;
    left: 0;
    right: 0;
    height: 62px;
    background: var(--brand-purple);
    display: flex;
    align-items: center;
    justify-content: space-between;
    padding: 0 22px 0 26px;
    box-sizing: border-box;
  }
  .brand-name {
    color: var(--brand-gold);
    font-weight: 300;
    font-size: 27px;
    letter-spacing: 1px;
    line-height: 1;
    margin: 0;
  }
  .brand-tagline {
    color: var(--muted-gold);
    font-weight: 300;
    font-size: 7px;
    letter-spacing: 2px;
    margin-top: 4px;
    white-space: nowrap;
  }
  .contact {
    display: flex;
    gap: 14px;
    color: var(--muted-gold);
    font-weight: 300;
    font-size: 7px;
    line-height: 11px;
    font-style: normal;
  }
  .contact-group { display: flex; flex-direction: column; }
  .contact-line { display: flex; align-items: center; gap: 4px; white-space: nowrap; }
  .contact-line svg { width: 6px; height: 6px; fill: var(--brand-gold); }
  .icon-spacer { width: 6px; display: inline-block; }
</style>
</head>
<body>
<div class="canvas">
  <article class="letterhead">
    <header class="header-band">
      <div class="brand">
        <h1 class="brand-name">PERI VALORE</h1>
        <div class="brand-tagline">CONSULTANCY &nbsp;Grace In Every Detail</div>
      </div>
      <address class="contact">
        <div class="contact-group">
          <span class="contact-line"><svg viewBox="0 0 10 10"><path d="M5 0a3.5 3.5 0 0 1 3.5 3.5C8.5 6 5 10 5 10S1.5 6 1.5 3.5A3.5 3.5 0 0 1 5 0z"/></svg>Harbour Lane No. 8</span>
          <span class="contact-line"><span class="icon-spacer"></span>Marina Quarter / 018940</span>
        </div>
        <div class="contact-group">
          <span class="contact-line"><svg viewBox="0 0 10 10"><rect x="2.5" y="0" width="5" height="10" rx="1"/></svg>0 987 654 321</span>
          <span class="contact-line"><svg viewBox="0 0 10 10"><rect x="0" y="2" width="10" height="7" rx="1"/></svg>0 987 654 322</span>
        </div>
        <div class="contact-group">
          <span class="contact-line"><svg viewBox="0 0 10 10"><rect x="0" y="2" width="10" height="6"/></svg>info@perivalore.com</span>
          <span class="contact-line"><svg viewBox="0 0 10 10"><circle cx="5" cy="5" r="4.5"/></svg>www.perivalore.com</span>
        </div>
      </address>
    </header>
  </article>
</div>
</body>
</html>
```